I need a flyer made , the flyer can be one page or two pages or three pages . I will be posting this on Instagram and social media platforms. I am a luxury home builder , I am looking to hire a construction project manager . Below are some examples and ideas what can be on the flyer

We’re looking for a construction project manager who’s passionate about building luxury homes at the highest standards
We’re hiring construction project manager
* Experience 5+ years in residential project management with a strong portfolio of completed homes.
* location : Bergen County NJ
* excellent leadership skills, leads teams with confidence and clarity
* communicates seamlessly with architects , engineers, designers and clients
*knows how to manage budgets and timelines without compromising quality
*solves problems with a positive solution first mindset
* pays attention to every detail because in luxury the small things are the big things

Apply now , link in bio or DM to connect.

My logo is attached, my web site www.velstridebuilders.com
My style is modern but still warm and inviting. I like a clean classy look .

Please don’t add any images of chairs or people to the flyer , I do not want people on my flyer. Do not add standard images of offices and houses , we are luxury builders , we build homes over 2 million dollars. Keep a classy , simple modern look . High end .

You can add a white hard hat with my logo on it for a image , this is a suggestion does not have to be on my flyer ,

```html
<!DOCTYPE html>
<html lang="en">
<head>
<meta charset="utf-8">
<title>Velstride Builders – We're Hiring</title>
<link rel="stylesheet" href="https://fonts.googleapis.com/css2?family=Great+Vibes&family=League+Spartan:wght@300;700;800;900&family=Poppins:wght@400;600;700;800&display=swap">
<style>
  :root {
    --ink: #000000;
    --panel-dark: #000000;
    --panel-soft: #2a2a2a;
    --pill-grey: #454545;
    --paper-light: #f7f7f7;
    --paper-shade: #e9e9e9;
    --white: #ffffff;
    --tick: #d9d9d9;
    --pin-red: #e51b1b;
    --pin-deep: #b80f12;
    --sketch-light: #f2f2f2;
    --sketch-shade: #dcdcdc;
  }
  * { box-sizing: border-box; margin: 0; padding: 0; }
  html, body { width: 1200px; height: 1200px; overflow: hidden; }
  body {
    position: relative;
    font-family: "Poppins", sans-serif;
    color: var(--ink);
    background:
      linear-gradient(160deg, var(--paper-light) 0%, var(--white) 30%, var(--paper-shade) 55%, var(--white) 75%, var(--paper-light) 100%);
  }
  .flyer { position: absolute; inset: 0; }

  .building-sketch {
    position: absolute; left: 774px; top: 118px; width: 426px; height: 533px;
    background: linear-gradient(200deg, var(--sketch-light) 0%, var(--sketch-shade) 60%, rgba(255,255,255,0) 100%);
    clip-path: polygon(32% 0, 100% 0, 100% 100%, 55% 100%, 0 88%, 0 70%, 25% 68%, 30% 20%);
  }

  .location-pin { position: absolute; left: 51px; top: 257px; width: 206px; height: 330px; }

  .headline-script {
    position: absolute; left: 272px; top: 96px;
    font-family: "Great Vibes", cursive; font-size: 190px; line-height: 1;
  }
  .headline-main {
    position: absolute; left: 268px; top: 262px;
    font-family: "League Spartan", sans-serif; font-weight: 900;
    font-size: 178px; line-height: 1; letter-spacing: -2px;
  }
  .role-line-one {
    position: absolute; left: 274px; top: 414px;
    font-family: "League Spartan", sans-serif; font-weight: 800;
    font-size: 58px; line-height: 1; letter-spacing: 0.5px;
  }
  .role-line-two {
    position: absolute; left: 272px; top: 468px;
    font-family: "League Spartan", sans-serif; font-size: 46px; line-height: 1;
  }
  .role-line-two .light { font-weight: 300; }
  .role-line-two .bold { font-weight: 800; }

  .motto { position: absolute; left: 272px; top: 530px; display: flex; gap: 3px; }
  .motto-pill {
    height: 52px; width: 213px; display: flex; align-items: center; justify-content: center;
    color: var(--white); font-family: "League Spartan", sans-serif; font-size: 22px;
  }
  .motto-pill b { font-weight: 800; margin-left: 6px; }
  .motto-pill.dark { background: var(--ink); border-radius: 26px 0 0 26px; }
  .motto-pill.grey { background: var(--pill-grey); border-radius: 0 26px 26px 0; }
  .motto-pill .light { font-weight: 300; }

  .requirements {
    position: absolute; left: 74px; top: 652px; width: 1051px; height: 289px;
    border-radius: 30px; overflow: hidden; display: flex;
  }
  .requirements-column { height: 100%; padding-top: 36px; }
  .requirements-column.left { width: 526px; background: var(--panel-dark); padding-left: 46px; padding-right: 40px; }
  .requirements-column.right { width: 525px; background: var(--panel-soft); padding-left: 24px; padding-right: 30px; }
  .requirement {
    list-style: none; position: relative; padding-left: 24px;
    color: var(--white); font-size: 19.5px; line-height: 24px; margin-bottom: 16px;
  }
  .requirement b { font-weight: 700; }
  .requirement .tick { position: absolute; left: 0; top: 6px; width: 15px; height: 15px; }

  .brand-name {
    position: absolute; left: 67px; top: 1020px; width: 326px; text-align: center;
    font-family: "Poppins", sans-serif; font-weight: 400; color: var(--ink);
    font-size: 50px; line-height: 1; letter-spacing: 2px;
  }
  .brand-name span { display: block; font-size: 27px; letter-spacing: 6px; margin-top: 14px; }

  .cta { position: absolute; left: 431px; top: 1006px; display: flex; align-items: center; }
  .cta-apply {
    width: 205px; height: 50px; background: var(--ink); color: var(--white);
    border-radius: 25px; display: flex; align-items: center; justify-content: center;
    font-weight: 700; font-size: 25px; position: relative; z-index: 1;
  }
  .cta-connect {
    width: 418px; height: 52px; margin-left: -4px; background: var(--white);
    border: 1.5px solid #555; border-radius: 26px;
    display: flex; align-items: center; justify-content: center;
    font-weight: 700; font-size: 24px;
  }

  .contact-label { position: absolute; top: 1072px; font-weight: 700; font-size: 20px; }
  .follow-label { left: 431px; }
  .visit-label { left: 833px; }
  .contact-divider { position: absolute; left: 822px; top: 1075px; width: 1px; height: 48px; background: var(--ink); }
  .contact-line { position: absolute; top: 1100px; font-size: 18px; display: flex; align-items: center; gap: 5px; }
  .contact-line .dot { width: 13px; height: 13px; border-radius: 50%; background: var(--ink); display: inline-block; }
  .handle-insta { left: 431px; }
  .handle-social { left: 648px; }
  .website { left: 833px; }
</style>
</head>
<body>
<main class="flyer">
  <div class="building-sketch" role="img" aria-label="Line sketch of a modern luxury two-storey home"></div>

  <svg class="location-pin" viewBox="0 0 206 330" aria-label="Location: Bergen County, NJ" role="img">
    <defs>
      <linearGradient id="pinBody" x1="0" y1="0" x2="1" y2="1">
        <stop offset="0" stop-color="#f0605a"/>
        <stop offset="0.45" stop-color="var(--pin-red)"/>
        <stop offset="1" stop-color="var(--pin-deep)"/>
      </linearGradient>
      <radialGradient id="pinShadow" cx="0.5" cy="0.5" r="0.5">
        <stop offset="0" stop-color="#000" stop-opacity="0.35"/>
        <stop offset="1" stop-color="#000" stop-opacity="0"/>
      </radialGradient>
    </defs>
    <ellipse cx="100" cy="310" rx="70" ry="10" fill="url(#pinShadow)"/>
    <path d="M103 4 C48 4 4 48 4 103 C4 160 50 220 110 315 C150 230 204 165 204 103 C204 48 158 4 103 4 Z" fill="url(#pinBody)"/>
    <circle cx="122" cy="104" r="56" fill="#ffffff"/>
    <text x="122" y="90" text-anchor="middle" font-family="Poppins, sans-serif" font-weight="700" font-size="19">Bergen</text>
    <text x="122" y="112" text-anchor="middle" font-family="Poppins, sans-serif" font-weight="700" font-size="19">County,</text>
    <text x="122" y="135" text-anchor="middle" font-family="Poppins, sans-serif" font-weight="700" font-size="19">NJ</text>
  </svg>

  <div class="headline-script">We're</div>
  <h1 class="headline-main">HIRING</h1>
  <div class="role-line-one">CONSTRUCTION</div>
  <div class="role-line-two"><span class="light">PROJECT</span> <span class="bold">MANAGER</span></div>

  <div class="motto">
    <div class="motto-pill dark"><span class="light">BUILD</span><b>LUXURY</b></div>
    <div class="motto-pill grey"><span class="light">LEAD</span><b>EXCELLENCE</b></div>
  </div>

  <section class="requirements">
    <ul class="requirements-column left">
      <li class="requirement"><svg class="tick" viewBox="0 0 16 16"><circle cx="8" cy="8" r="8" fill="var(--tick)"/><path d="M4.5 8.2 7 10.6 11.5 5.6" fill="none" stroke="#000" stroke-width="2"/></svg>Experience <b>5+ years</b> in residential project management with a strong portfolio of completed homes.</li>
      <li class="requirement"><svg class="tick" viewBox="0 0 16 16"><circle cx="8" cy="8" r="8" fill="var(--tick)"/><path d="M4.5 8.2 7 10.6 11.5 5.6" fill="none" stroke="#000" stroke-width="2"/></svg>Excellent <b>leadership skills</b>, leads teams with confidence and clarity</li>
      <li class="requirement"><svg class="tick" viewBox="0 0 16 16"><circle cx="8" cy="8" r="8" fill="var(--tick)"/><path d="M4.5 8.2 7 10.6 11.5 5.6" fill="none" stroke="#000" stroke-width="2"/></svg><b>Communicates seamlessly</b> with architects , engineers, designers and clients</li>
    </ul>
    <ul class="requirements-column right">
      <li class="requirement"><svg class="tick" viewBox="0 0 16 16"><circle cx="8" cy="8" r="8" fill="var(--tick)"/><path d="M4.5 8.2 7 10.6 11.5 5.6" fill="none" stroke="#2a2a2a" stroke-width="2"/></svg>Knows how to <b>manage budgets and timelines</b> without compromising quality</li>
      <li class="requirement"><svg class="tick" viewBox="0 0 16 16"><circle cx="8" cy="8" r="8" fill="var(--tick)"/><path d="M4.5 8.2 7 10.6 11.5 5.6" fill="none" stroke="#2a2a2a" stroke-width="2"/></svg><b>Solves problems</b> with a positive solution first mindset</li>
      <li class="requirement"><svg class="tick" viewBox="0 0 16 16"><circle cx="8" cy="8" r="8" fill="var(--tick)"/><path d="M4.5 8.2 7 10.6 11.5 5.6" fill="none" stroke="#2a2a2a" stroke-width="2"/></svg><b>Pays attention to every detail</b> because in luxury the small things are the big things</li>
    </ul>
  </section>

  <div class="brand-name">VELSTRIDE<span>builders</span></div>

  <div class="cta">
    <div class="cta-apply">Apply now</div>
    <div class="cta-connect">Link in bio or DM to connect</div>
  </div>

  <div class="contact-label follow-label">Follow us</div>
  <div class="contact-line handle-insta"><span class="dot"></span>velstridebuilders</div>
  <div class="contact-line handle-social"><span class="dot"></span>VelstrideDevs</div>
  <div class="contact-divider"></div>
  <div class="contact-label visit-label">Visit us</div>
  <div class="contact-line website">www.velstridebuilders.com</div>
</main>
</body>
</html>
```